Professional Services - letterhead / business cards

The company (velmora partners) will provide services to Investment Funds and large investors in Spain. I have recently chosen a logo that I am attaching.

I would like a simple stationary design that i could use as letter head, business cards and "with compliments" cards.

I am not quite sure which color I will mostly use for the logo, in the email signature I will probably lean towards the white background and grey letters. I am attaching my favourite options.

Target Market(s)

Large Multinationals, Investment funds and Law firms

Industry/Entity Type

Business

Requirements
Must have
• my details are:
Luis R. Abadal
Velmora Partners S.L.
Casa de Torrelumbre
Calle de Vientoalto 27
28014 Madrid
T: +34 (91) 387-2265
M: +34 (646) 819-054
e-mail: labadal@velmorapartners.com

```html
<!DOCTYPE html>
<html lang="en">
<head>
<meta charset="utf-8">
<title>Velmora Partners – Stationery</title>
<link href="https://fonts.googleapis.com/css2?family=PT+Sans:wght@400;700&family=Lobster&display=swap" rel="stylesheet">
<style>
  :root{
    --navy:#27286b;
    --grey:#a9abae;
    --paper:#ffffff;
    --paper-shade:#eeeeef;
    --backdrop:#e4e1dc;
    --ink-soft:#555761;
    --shadow:0 2px 6px rgba(0,0,0,.18);
  }
  *{box-sizing:border-box;margin:0;padding:0}
  html,body{width:1200px;height:468px;overflow:hidden}
  body{background:var(--backdrop);font-family:"PT Sans",Arial,sans-serif;color:var(--navy);position:relative}

  .sheet{position:absolute;background:var(--paper);box-shadow:var(--shadow);overflow:hidden}
  .brand-name{position:absolute;font-family:"PT Sans",Arial,sans-serif;font-weight:400;color:var(--navy);white-space:nowrap;letter-spacing:.2px}
  .brand-name.on-dark{color:var(--paper)}

  /* footer band: navy strip with slanted end, grey strip to the right */
  .band{position:absolute;left:0;right:0}
  .band-navy{position:absolute;left:0;top:0;bottom:0;background:var(--navy);color:var(--paper);
    clip-path:polygon(0 0,calc(100% - 12px) 0,100% 100%,0 100%);display:flex;align-items:center}
  .band-grey{position:absolute;right:0;top:0;bottom:0;background:var(--grey);color:var(--paper);
    clip-path:polygon(0 0,100% 0,100% 100%,12px 100%);display:flex;align-items:center;justify-content:flex-end}
  .band-text{font-size:6.5px;white-space:nowrap}

  .icon{width:6px;height:6px;display:inline-block;vertical-align:-1px;margin-right:2px}

  /* letterhead */
  .letterhead{left:4px;top:13px;width:336px;height:434px;background:linear-gradient(160deg,#fff 40%,var(--paper-shade))}
  .letterhead .brand-name{left:0;right:0;top:18px;text-align:center;font-size:19px}
  .letterhead .band{top:411px;height:13px}
  .letterhead .band-navy{width:82%;padding-left:16px}
  .letterhead .band-grey{width:21%;padding-right:10px}

  /* envelopes */
  .envelope{width:377px;height:168px;background:linear-gradient(170deg,#fff 35%,var(--paper-shade))}
  .envelope svg{position:absolute;left:0;top:0}
  .envelope-back{left:454px;top:14px}
  .envelope-back .brand-name{left:0;right:0;top:24px;text-align:center;font-size:19px}
  .envelope-open{left:373px;top:86px}
  .envelope-open .brand-name{left:0;right:0;top:28px;text-align:center;font-size:21px}
  .envelope-front{left:412px;top:162px;border:1px solid #ddd}
  .envelope-front .brand-name{left:10px;top:22px;font-size:18px}
  .envelope-front .band{top:149px;height:10px}
  .envelope-front .band-navy{width:85%;padding-left:11px}
  .envelope-front .band-grey{width:16%}

  /* compliments slip */
  .compliments{left:864px;top:163px;width:328px;height:154px}
  .compliments .brand-name{left:0;right:0;top:28px;text-align:center;font-size:21px}
  .compliments .band{top:106px;height:11px}
  .compliments .band-navy{width:86%;justify-content:center}
  .compliments .band-grey{width:17%}
  .compliments-title{position:absolute;left:0;right:0;top:120px;text-align:center;font-family:"Lobster",cursive;font-size:16px;color:var(--navy)}
  .compliments-contacts{position:absolute;left:0;right:0;top:140px;text-align:center;font-size:6px;color:var(--ink-soft)}
  .compliments-contacts span{margin:0 3px}
  .caption{position:absolute;left:864px;width:328px;top:326px;text-align:center;font-size:18px;color:var(--paper);text-shadow:0 1px 2px rgba(0,0,0,.35)}

  /* business cards */
  .card{top:366px;width:170px;height:96px}
  .card .brand-name{left:0;right:0;top:18px;text-align:center;font-size:14px}
  .card .band{top:51px;height:9px}
  .card .band-navy{width:74%;padding-left:4px}
  .card .band-grey{width:30%;padding-right:4px}
  .card-holder{font-size:7px;font-weight:700;white-space:nowrap}
  .card-holder small{font-size:4.5px;font-weight:400;margin-left:2px}
  .card .band-grey .band-text{font-size:4.5px}
  .card-details{position:absolute;left:0;right:0;top:66px;font-size:4.6px;color:var(--ink-soft);line-height:1.5}
  .card-one{left:375px}
  .card-one .card-address{position:absolute;left:0;width:82px;text-align:right;padding-right:6px;border-right:.6px solid #bbb}
  .card-one .card-reach{position:absolute;left:88px}
  .card-two{left:563px}
  .card-two .card-details{text-align:center}
  .card-plain{left:740px}
  .card-plain .brand-name,.card-dark .brand-name{top:40px;font-size:16px}
  .card-dark{left:917px;background:var(--navy)}
</style>
</head>
<body>

<!-- Letterhead -->
<section class="sheet letterhead" aria-label="Letterhead">
  <p class="brand-name">velmora partners</p>
  <div class="band">
    <div class="band-navy"><span class="band-text">Casa de Torrelumbre, Calle de Vientoalto 27 28014 Madrid</span></div>
    <div class="band-grey"><span class="band-text">
      <svg class="icon" viewBox="0 0 10 10"><circle cx="5" cy="5" r="4.3" fill="none" stroke="#fff" stroke-width="1"/><path d="M3.3 2.6l1 1-.5.7c.4.8 1 1.4 1.8 1.8l.7-.5 1 1-.7.9C4.6 7.3 2.7 5.4 2.5 3.3z" fill="#fff"/></svg>+34 (91) 387-2265</span></div>
  </div>
</section>

<!-- Envelope, back with navy flap -->
<section class="sheet envelope envelope-back" aria-label="Envelope back">
  <svg width="377" height="168" viewBox="0 0 377 168">
    <path d="M0 0H377V4C372 22 366 30 346 38L214 76Q188 84 162 76L30 38C10 30 4 22 0 4Z" fill="var(--navy)"/>
  </svg>
  <p class="brand-name on-dark">velmora</p>
</section>

<!-- Envelope, open flap -->
<section class="sheet envelope envelope-open" aria-label="Envelope flap">
  <svg width="377" height="168" viewBox="0 0 377 168">
    <path d="M1 0V6C4 22 10 28 30 36L162 74Q188 82 214 74L346 36C366 28 373 22 376 6V0" fill="none" stroke="#333" stroke-width="1"/>
  </svg>
  <p class="brand-name">velmora</p>
</section>

<!-- Envelope, front -->
<section class="sheet envelope envelope-front" aria-label="Envelope front">
  <p class="brand-name">velmora partners</p>
  <div class="band">
    <div class="band-navy"><span class="band-text">Casa de Torrelumbre, Calle de Vientoalto 27, 28014 Madrid</span></div>
    <div class="band-grey"></div>
  </div>
</section>

<!-- With compliments slip -->
<section class="sheet compliments" aria-label="With compliments slip">
  <p class="brand-name">velmora partners</p>
  <div class="band">
    <div class="band-navy"><span class="band-text">Casa de Torrelumbre, Calle de Vientoalto 27, 28014 Madrid</span></div>
    <div class="band-grey"></div>
  </div>
  <p class="compliments-title">With Compliments</p>
  <p class="compliments-contacts">
    <span>+34 (91) 387-2265</span><span>+34 (646) 819-054</span><span>labadal@velmorapartners.com</span>
  </p>
</section>
<p class="caption">Compliments</p>

<!-- Business card, address layout -->
<section class="sheet card card-one" aria-label="Business card front">
  <p class="brand-name">velmora partners</p>
  <div class="band">
    <div class="band-navy"><span class="card-holder">Luis R. Abadal,<small>Velmora Partners S.L.</small></span></div>
    <div class="band-grey"><span class="band-text">+34 (91) 387-2265</span></div>
  </div>
  <div class="card-details">
    <p class="card-address">Casa de Torrelumbre<br>Calle de Vientoalto 27<br>28014 Madrid</p>
    <p class="card-reach">+34 (646) 819-054<br>labadal@velmorapartners.com</p>
  </div>
</section>

<!-- Business card, single-line layout -->
<section class="sheet card card-two" aria-label="Business card front, alternative">
  <p class="brand-name">velmora partners</p>
  <div class="band">
    <div class="band-navy"><span class="card-holder">Luis R. Abadal,<small>Velmora Partners S.L.</small></span></div>
    <div class="band-grey"><span class="band-text">+34 (91) 387-2265</span></div>
  </div>
  <div class="card-details">
    <p>+34 (646) 819-054 &nbsp; labadal@velmorapartners.com</p>
    <p>Casa de Torrelumbre, Calle de Vientoalto 27, 28014 Madrid</p>
  </div>
</section>

<!-- Business card backs -->
<section class="sheet card card-plain" aria-label="Business card back, white">
  <p class="brand-name">velmora partners</p>
</section>
<section class="sheet card card-dark" aria-label="Business card back, navy">
  <p class="brand-name on-dark">velmora partners</p>
</section>

</body>
</html>
```